Menu Design Project

My Restaurant is called The Platter Corner, it's fast food restaurant serves Gyro, Wings, Subs, Fried Seafood and chicken tenders. I'm looking for a menu design to fit the fast food category and have some photos of the food on the front page as well inside the menu. I will attached some photos and you can add any other photo related to the menu from the web.

Industry/Entity Type

Restaurant

```html
<!DOCTYPE html>
<html lang="en">
<head>
<meta charset="utf-8">
<title>The Platter Corner – Menu</title>
<link rel="stylesheet" href="https://fonts.googleapis.com/css2?family=Open+Sans:wght@400;600;700&family=Oswald:wght@300;400;500&family=Montserrat:wght@600;700&display=swap">
<style>
:root{
  --red:#e30613;
  --red-dark:#c00010;
  --ink:#1d1d1d;
  --paper:#f4f4f5;
  --paper-shade:#e7e7ea;
  --backdrop:#ead5dd;
  --white:#ffffff;
}
*{box-sizing:border-box;margin:0;padding:0}
html,body{width:1200px;height:900px;overflow:hidden}
body{background:var(--backdrop);font-family:"Open Sans",Arial,sans-serif;color:var(--ink);position:relative}

.sheet{position:absolute;display:flex;flex-direction:column;gap:4px}
.sheet--outside{left:85px;top:140px;width:510px}
.sheet--inside{left:645px;top:140px;width:480px}

.panel{position:relative;height:308px;background:linear-gradient(135deg,var(--white) 0%,var(--paper) 45%,var(--paper-shade) 100%);box-shadow:0 2px 6px rgba(0,0,0,.12);overflow:hidden}
.panel__frame{position:absolute;inset:8px 10px 8px 10px;border:3px solid var(--red);pointer-events:none}
.panel--back{transform:rotate(180deg)}

.photo{position:absolute;border-radius:6px}
.photo--wings{background:radial-gradient(circle at 50% 50%,#d9782f,#a8481c 65%,transparent 72%)}
.photo--burger{background:radial-gradient(ellipse at 50% 50%,#b56a2a,#6b3a18 55%,#4e8a2c 62%,transparent 72%)}
.photo--gyro{background:radial-gradient(ellipse at 50% 50%,#d8b78a,#8a5a38 60%,transparent 72%)}
.photo--cans{background:linear-gradient(90deg,#b3121d 0 20%,#2e8b3a 20% 45%,#f07e1a 45% 70%,#d9d9d9 70% 85%,#c5101a 85% 100%);border-radius:8px;opacity:.85}
.photo--bowl{background:radial-gradient(ellipse at 50% 35%,var(--red),#a0000a 60%,transparent 70%)}
.photo--combo-left{background:radial-gradient(ellipse at 50% 55%,#e8b34a,#c54a1d 50%,#b3121d 60%,transparent 72%)}
.photo--combo-right{background:radial-gradient(ellipse at 50% 55%,#f0c24d,#c98a32 50%,#b3121d 62%,transparent 72%)}
.map{position:absolute;left:298px;top:58px;width:195px;height:150px;border:2px solid #8b8f96;border-radius:14px;background:linear-gradient(160deg,#f2f2f0,#e4e6e8)}

.cover__mark{position:absolute;left:50%;top:22px;width:54px;height:54px;margin-left:-27px;border:4px solid var(--red);border-radius:50%}
.cover__name{position:absolute;left:0;right:0;top:84px;text-align:center;font:700 16px/1 "Open Sans",sans-serif;color:var(--ink)}
.cover__title{position:absolute;left:0;right:0;top:106px;text-align:center;font:400 25px/1 "Oswald",sans-serif;color:var(--red)}
.cover__hours-label{position:absolute;left:0;right:0;top:152px;text-align:center;font:400 10px/1 "Open Sans",sans-serif}
.cover__hours{position:absolute;left:0;right:0;top:168px;text-align:center;font:400 10px/1 "Open Sans",sans-serif;color:var(--red)}
.bar{position:absolute;left:0;right:0;background:var(--red);color:var(--white);display:flex;align-items:center;justify-content:center;gap:8px}
.cover__bar{bottom:8px;height:22px;font:400 12px/1 "Montserrat",sans-serif;letter-spacing:.3px}
.bar svg{width:11px;height:11px;fill:none;stroke:var(--white);stroke-width:2}

.back__slogan{top:22px;height:22px;font:400 17px/1 "Oswald",sans-serif;letter-spacing:1px}
.tag{position:absolute;height:16px;background:var(--red);color:var(--white);font:700 10px/16px "Montserrat",sans-serif;letter-spacing:1px;padding:0 10px;display:flex;align-items:center;gap:6px;text-transform:uppercase;white-space:nowrap}
.tag__dot{width:8px;height:8px;border-radius:50%;border:1.5px solid var(--white);flex:none}
.back__drinks-tag{left:28px;top:57px;width:88px}
.back__drinks{position:absolute;left:30px;top:76px;font:400 9px/15px "Open Sans",sans-serif}
.back__call{position:absolute;left:40px;width:190px;top:246px;text-align:center;font:400 9px/1 "Open Sans",sans-serif}
.back__phone{position:absolute;left:40px;width:190px;top:260px;text-align:center;font:700 10px/1 "Oswald",sans-serif;color:var(--red);letter-spacing:.5px}
.back__hours{position:absolute;left:320px;top:232px;width:150px;text-align:center;font:400 10px/14px "Open Sans",sans-serif}
.back__hours span{color:var(--red);display:block}
.back__rule{position:absolute;left:40px;right:26px;top:276px;border-top:1.5px solid #8b8f96}
.back__address{position:absolute;left:0;right:0;top:284px;display:flex;justify-content:center;gap:14px;font:400 11px/1 "Montserrat",sans-serif}
.back__address svg{width:10px;height:10px;fill:none;stroke:var(--red);stroke-width:2;vertical-align:-1px}

.menu__mark{position:absolute;left:50%;top:18px;width:32px;height:32px;margin-left:-16px;border:3px solid var(--red);border-radius:50%}
.menu__title{position:absolute;left:0;right:0;top:58px;text-align:center;font:700 11px/1 "Open Sans",sans-serif;color:var(--red)}
.menu__tag--left{left:4px;border-radius:0 4px 4px 0}
.menu__tag--right{right:4px;border-radius:4px 0 0 4px}
.list{position:absolute;display:grid;row-gap:0;font:400 9px/13.8px "Open Sans",sans-serif}
.list__row{display:flex;justify-content:space-between;white-space:nowrap}
.list__note{color:var(--red);font-size:8.5px}
.cheese{position:absolute;font:400 5px/1 "Open Sans",sans-serif;color:var(--red);white-space:nowrap}
.combo-tag small{font-size:6.5px;letter-spacing:.3px}
.kids__tag{position:absolute;left:188px;top:193px;width:106px;height:14px;justify-content:center;border-radius:2px;font-size:9px;line-height:14px}
.kids{position:absolute;left:130px;top:220px;width:250px;font:400 9px/14px "Open Sans",sans-serif;text-align:center}
.kids b{color:var(--red);font-weight:700;margin-left:6px}
</style>
</head>
<body>

<section class="sheet sheet--outside">
  <article class="panel panel--back" aria-label="Back cover">
    <div class="panel__frame"></div>
    <div class="bar back__slogan">GOOD FOOD, GOOD MOOD</div>

    <div class="tag back__drinks-tag"><span class="tag__dot"></span>Drinks</div>
    <p class="back__drinks">Cola, Diet Cola,<br>Lemon-Lime, Sports Drink,<br>Orange Soda,<br>Strawberry Soda,<br>Cherry Spice and more.</p>
    <div class="photo photo--cans" role="img" aria-label="Photo of assorted soda cans" style="left:168px;top:58px;width:98px;height:96px"></div>

    <div class="photo photo--bowl" role="img" aria-label="Illustration of a red bowl with fork and knife" style="left:105px;top:166px;width:52px;height:74px"></div>
    <p class="back__call">Call Us for Pick Up orders or Catering</p>
    <p class="back__phone">555-310-2274</p>

    <div class="map" role="img" aria-label="Street map showing the restaurant location"></div>
    <p class="back__hours">Hours of operation:<span>Monday to Sunday 11am-9pm</span></p>

    <div class="back__rule"></div>
    <p class="back__address">
      <span><svg viewBox="0 0 12 12"><circle cx="6" cy="6" r="5"/><circle cx="6" cy="5" r="1.5"/></svg> 4120 Harbor Market Ave, Lakeview, TX 77410</span>
      <span><svg viewBox="0 0 12 12"><circle cx="6" cy="6" r="5"/><path d="M4 3.5l1 1.5-.6.8a4 4 0 0 0 1.8 1.8l.8-.6 1.5 1"/></svg> 555-310-2274</span>
    </p>
  </article>

  <article class="panel panel--cover" aria-label="Front cover">
    <div class="panel__frame"></div>
    <div class="cover__mark"></div>
    <h1 class="cover__name">The Platter Corner</h1>
    <p class="cover__title">The Platter Corner Restaurant</p>
    <p class="cover__hours-label">Hours of operation:</p>
    <p class="cover__hours">Monday to Sunday 11am-9pm</p>
    <div class="photo photo--wings" role="img" aria-label="Photo of fried chicken wings" style="left:30px;top:198px;width:120px;height:82px"></div>
    <div class="photo photo--burger" role="img" aria-label="Photo of a cheeseburger" style="left:200px;top:196px;width:112px;height:84px"></div>
    <div class="photo photo--gyro" role="img" aria-label="Photo of a gyro wrap" style="left:365px;top:186px;width:124px;height:96px"></div>
    <div class="bar cover__bar">
      <svg viewBox="0 0 12 12"><circle cx="6" cy="6" r="5"/><circle cx="6" cy="5" r="1.5"/></svg>
      <span>4120 Harbor Market Ave, Lakeview, TX 77410</span>
      <svg viewBox="0 0 12 12"><circle cx="6" cy="6" r="5"/><path d="M4 3.5l1 1.5-.6.8a4 4 0 0 0 1.8 1.8l.8-.6 1.5 1"/></svg>
      <span>555-310-2274</span>
    </div>
  </article>
</section>

<section class="sheet sheet--inside">
  <article class="panel" aria-label="Menu page one">
    <div class="panel__frame"></div>
    <div class="menu__mark"></div>
    <h2 class="menu__title">The Platter Corner Menu</h2>

    <div class="tag menu__tag--left" style="top:64px;width:100px"><span class="tag__dot"></span>Chicken</div>
    <div class="list" style="left:24px;top:84px;width:168px">
      <div class="list__row"><span>10 Large Wings</span><span>$8.99</span></div>
      <div class="list__row"><span>20 Large Wings</span><span>$16.99</span></div>
      <div class="list__row"><span>30 Large Wings</span><span>$23.99</span></div>
      <div class="list__row"><span>50 Large Wings</span><span>$39.99</span></div>
      <div class="list__row"><span>½ lb. Chicken Strips</span><span>$5.49</span></div>
      <div class="list__row"><span>1lb. Chicken Strips</span><span>$7.99</span></div>
      <div class="list__row"><span>½ lb. Gizzards</span><span>$5.49</span></div>
      <div class="list__row"><span>1lb. Gizzards</span><span>$7.99</span></div>
    </div>

    <div class="tag menu__tag--left" style="top:204px;width:100px"><span class="tag__dot"></span>Seafood</div>
    <div class="list" style="left:24px;top:222px;width:168px">
      <div class="list__row"><span>½ lb. Shrimp</span><span>$7.99</span></div>
      <div class="list__row"><span>1lb. Shrimp</span><span>$13.99</span></div>
      <div class="list__row"><span>½ lb. Fish</span><span>$6.99</span></div>
      <div class="list__row"><span>1lb. Fish</span><span>$12.99</span></div>
    </div>

    <div class="tag menu__tag--right" style="top:66px"><span>Fresh Salad</span><span class="tag__dot"></span></div>
    <div class="list" style="left:230px;top:84px;width:224px">
      <div class="list__row"><span>Caesar Salad</span><span>$4.95</span></div>
      <div class="list__row"><span>Gyro Salad</span><span>$5.95</span></div>
      <div class="list__row"><span>Shrimp Caesar Salad</span><span>$6.25</span></div>
      <div class="list__row"><span>Greek Salad</span><span>$5.95</span></div>
    </div>

    <div class="tag menu__tag--right" style="top:148px"><span>Gyro &amp; Subs</span><span class="tag__dot"></span></div>
    <div class="list" style="left:230px;top:168px;width:224px">
      <div class="list__row"><span>Gyro (Original or Chicken)</span><span>$6.99</span></div>
      <div class="list__row"><span>¼ lb. Black Angus Burger</span><span>$3.99</span></div>
      <div class="list__row"><span>Buffalo Chicken Sandwich</span><span>$5.99</span></div>
      <div class="list__row list__note"><span>YOUR CHOICE OF 6" OR FOOTLONG SUBS</span></div>
      <div class="list__row"><span>Po Boy Shrimp</span><span>$7.55-$9.25</span></div>
      <div class="list__row"><span>Philly (Steak or Chicken)</span><span>$6.75-$8.99</span></div>
      <div class="list__row"><span>Fish</span><span>$6.75-$8.99</span></div>
      <div class="list__row"><span>Turkey &amp; Cheese</span><span>$6.49-$7.95</span></div>
    </div>
  </article>

  <article class="panel" aria-label="Menu page two">
    <div class="panel__frame"></div>

    <div class="tag menu__tag--left" style="top:20px;width:96px"><span class="tag__dot"></span>Sides</div>
    <div class="list" style="left:30px;top:40px;width:150px">
      <div class="list__row"><span>French Fries</span><span>$2.79</span></div>
      <div class="list__row"><span>Cajun Fries</span><span>$3.99</span></div>
      <div class="list__row"><span>Onion Rings</span><span>$4.99</span></div>
      <div class="list__row"><span>5 Jalapeno Poppers</span><span>$4.99</span></div>
      <div class="list__row"><span>Fried Okra</span><span>$4.99</span></div>
      <div class="list__row"><span>Fried Mushroom</span><span>$5.49</span></div>
      <div class="list__row"><span>5 Mozzarella Sticks</span><span>$5.49</span></div>
    </div>

    <div class="tag menu__tag--right combo-tag" style="top:22px"><span>Combos <small>Includes 16oz Soft Drink!</small></span><span class="tag__dot"></span></div>
    <div class="list" style="left:236px;top:42px;width:190px">
      <div class="list__row"><span>½ lb. Fish &amp; Fries</span><span>$9.99</span></div>
      <div class="list__row"><span>½ lb. Shrimp &amp; Fries</span><span>$10.99</span></div>
      <div class="list__row"><span>6" Philly (Steak or Chicken) &amp; Fries</span><span>$9.99</span></div>
      <div class="list__row"><span>Gyro (Original, Chicken or Fish) &amp;Fries</span><span>$9.49</span></div>
      <div class="list__row"><span>5 Wings &amp; Fries</span><span>$9.49</span></div>
      <div class="list__row"><span>½ lb. Gizzards &amp; Fries</span><span>$7.99</span></div>
      <div class="list__row"><span>¼ lb. Black Angus Burger &amp; Fries</span><span>$6.99</span></div>
      <div class="list__row"><span>5 Wings &amp; Gizzards</span><span>$11.49</span></div>
      <div class="list__row"><span>½ lb. Chicken Strips &amp; Fries</span><span>$7.99</span></div>
    </div>
    <span class="cheese" style="left:430px;top:130px">*CHEESE EXTRA</span>

    <div class="tag kids__tag">Kids Meal</div>
    <div class="photo photo--combo-left" role="img" aria-label="Photo of a burger, fries, soda cup and chicken nuggets" style="left:22px;top:208px;width:120px;height:90px"></div>
    <div class="kids">
      <div>Chicken Nuggets 4pc with small drink and fries <b>$4.95</b></div>
      <div>Chicken Strips 2pc with small drink and fries <b>$4.95</b></div>
      <div>Mac &amp; Cheese <b>$3.95</b></div>
    </div>
    <div class="photo photo--combo-right" role="img" aria-label="Photo of fries, chicken strips and a soda cup" style="left:362px;top:210px;width:100px;height:80px"></div>
  </article>
</section>

</body>
</html>
```